Business Card Design for Training Business

Clear Path Coaching is a new business that delivers training and other services with a focus on topics related to mental health and wellbeing, for example, Wellmind Response Course, Resilience etc. We have a strong focus on evidence-based psychology and neuroscience. I have a logo which I will upload with the brief, so please consider colours that work well with the logo.
Target Market(s)
Adults, workplaces (particularly government and not-for-profits)
Industry/Entity Type
Business
Contact Information for Business Card
Head Strong TrainingSamantha SellwoodDirector0438 770 850sam@headstrongtraining.com.auwww.headstrongtraining.com.au

```html
<!DOCTYPE html>
<html lang="en">
<head>
<meta charset="utf-8">
<title>Clear Path Coaching – Business Card</title>
<link rel="stylesheet" href="https://fonts.googleapis.com/css2?family=Questrial&display=swap">
<style>
  :root {
    --backdrop: #3b3b3b;
    --card: #f7f7f7;
    --teal: #22b7be;
    --teal-line: #3fc3c8;
    --curve-rule: #a68c8c;
    --ink-soft: #6a6a6a;
    --ink-web: #555555;
    --white: #ffffff;
  }
  * { box-sizing: border-box; margin: 0; padding: 0; }
  html, body { width: 1200px; height: 750px; overflow: hidden; }
  body {
    background: var(--backdrop);
    font-family: "Questrial", "Century Gothic", sans-serif;
    position: relative;
  }
  .card {
    position: absolute;
    left: 371px;
    width: 461px;
    height: 262px;
    background: var(--card);
    border-radius: 14px;
    overflow: hidden;
  }
  .card--front { top: 106px; }
  .card--back { top: 387px; }

  .brand-mark {
    position: absolute;
    left: 50%;
    transform: translateX(-50%);
    border: 1.5px solid var(--teal-line);
    border-radius: 50%;
  }
  .card--front .brand-mark { top: 16px; width: 72px; height: 72px; }
  .card--back .brand-mark { top: 66px; width: 68px; height: 68px; }

  .brand-name {
    position: absolute;
    left: 0; right: 0;
    text-align: center;
    color: var(--ink-soft);
    font-weight: 400;
    text-transform: uppercase;
    line-height: 1;
  }
  .card--front .brand-name--main { top: 100px; font-size: 22px; letter-spacing: 2.5px; }
  .card--front .brand-name--sub { top: 129px; font-size: 11px; letter-spacing: 5px; padding-left: 5px; }
  .card--back .brand-name--main { top: 150px; font-size: 18px; letter-spacing: 2px; }

  .band { position: absolute; left: 0; top: 0; width: 461px; height: 262px; }

  .person {
    position: absolute;
    left: 0; right: 0;
    text-align: center;
    color: var(--white);
    line-height: 1;
  }
  .person__name { top: 174px; font-size: 19px; letter-spacing: 0.3px; }
  .person__role { top: 196px; font-size: 14px; }

  .contact {
    position: absolute;
    left: 0; right: 0;
    display: flex;
    justify-content: center;
    align-items: center;
    gap: 16px;
    color: var(--white);
    font-size: 12.5px;
    line-height: 1;
  }
  .contact--row1 { top: 219px; }
  .contact--row2 { top: 237px; }
  .contact__item { display: flex; align-items: center; gap: 5px; }
  .contact__icon { width: 12px; height: 12px; flex: none; }

  .web-back {
    position: absolute;
    left: 0; right: 0;
    top: 227px;
    text-align: center;
    color: var(--ink-web);
    font-size: 13px;
    line-height: 1;
  }
</style>
</head>
<body>

  <section class="card card--front" aria-label="Business card front">
    <span class="brand-mark" aria-hidden="true"></span>
    <div class="brand-name brand-name--main">Clear Path</div>
    <div class="brand-name brand-name--sub">Coaching</div>

    <svg class="band" viewBox="0 0 461 262" aria-hidden="true">
      <path d="M0 200 Q230 110 461 206 L461 262 L0 262 Z" fill="var(--teal)"/>
      <path d="M0 200 Q230 110 461 206" fill="none" stroke="var(--curve-rule)" stroke-width="2"/>
    </svg>

    <div class="person person__name">Rebecca Tanfield</div>
    <div class="person person__role">Director</div>

    <div class="contact contact--row1">
      <span class="contact__item">
        <svg class="contact__icon" viewBox="0 0 24 24" aria-hidden="true">
          <path fill="#fff" d="M6.6 10.8c1.4 2.8 3.8 5.1 6.6 6.6l2.2-2.2c.3-.3.7-.4 1-.2 1.1.4 2.3.6 3.6.6.6 0 1 .4 1 1V20c0 .6-.4 1-1 1C10.6 21 3 13.4 3 4c0-.6.4-1 1-1h3.5c.6 0 1 .4 1 1 0 1.3.2 2.5.6 3.6.1.3 0 .7-.2 1L6.6 10.8z"/>
        </svg>
        0491 362 517
      </span>
      <span class="contact__item">
        <svg class="contact__icon" viewBox="0 0 24 24" aria-hidden="true">
          <rect x="2" y="5" width="20" height="14" rx="1" fill="#fff"/>
          <path d="M2 6 L12 13 L22 6" fill="none" stroke="var(--teal)" stroke-width="1.8"/>
        </svg>
        bec@clearpathcoaching.example.au
      </span>
    </div>
    <div class="contact contact--row2">
      <span class="contact__item">
        <svg class="contact__icon" viewBox="0 0 24 24" aria-hidden="true">
          <circle cx="12" cy="12" r="10" fill="#fff"/>
          <path d="M2 12h20M12 2c3 3 3 17 0 20M12 2c-3 3-3 17 0 20" fill="none" stroke="var(--teal)" stroke-width="1.5"/>
        </svg>
        www.clearpathcoaching.example.au
      </span>
    </div>
  </section>

  <section class="card card--back" aria-label="Business card back">
    <span class="brand-mark" aria-hidden="true"></span>
    <div class="brand-name brand-name--main">Clear Path Coaching</div>
    <div class="web-back">www.clearpathcoaching.example.au</div>
  </section>

</body>
</html>
```